Create a Dynamic Website for Roadhaven 41Ter!

Dear designers,
We have an exciting design opportunity for you on PixelBazaar. We are in need of a creative and professional website design for our company, Roadhaven 41Ter. Our current website is outdated and fails to convey the image we want to project. We are determined to revamp our online presence and create a website that truly represents who we are.
Roadhaven 41Ter is a versatile establishment offering a Velko Express, sandwich bar, restaurant, parking facilities, and meeting rooms. Each of these aspects deserves its own spotlight on our website. Therefore, we are seeking a WordPress-based website design that allows us to easily make changes, modify texts, and add new content as needed.
It is crucial that the design aligns seamlessly with our new branding and style. We invite you to explore our Instagram (@Roadhaven41ter) and Facebook (@Roadhaven) pages to gain an understanding of our branding and incorporate those elements into the design.
You can find our current website at www.guardedroadhaven.eu, but we want a new website that is vibrant, dynamic, and includes moving elements if possible. We believe this will enhance the user experience and keep visitors engaged for longer periods.
Key elements we would like to include in the new website design are as follows:
Clear presentation of all our services: Velko Express, sandwich bar, restaurant, parking facilities, and meeting rooms.
Easy navigation for visitors to find information effortlessly.
Engaging call-to-action buttons that encourage visitors to take specific actions, such as reserving a meeting room or placing an order.
A dedicated blog section where we can share news, events, and special offers.
Integration of a contact form and contact details for easy communication with our visitors.
Responsive design that works seamlessly across desktop and mobile devices.
We envision a modern and visually appealing website that leaves a lasting positive impression on visitors. We are interested in a design that incorporates creative visual elements and provides a user-friendly interface.
Thank you for your time, and we eagerly await your designs.
Best regards,

```html
<!DOCTYPE html>
<html lang="en">
<head>
<meta charset="utf-8">
<title>Contact – Roadhaven 41Ter</title>
<link rel="stylesheet" href="https://fonts.googleapis.com/css2?family=Poppins:wght@400;500;600;700&display=swap">
<style>
:root{
  --blue:#1a7fc8;
  --navy:#14215e;
  --hero:#2c3a72;
  --ink:#111;
  --text:#666;
  --field:#f3f3f3;
  --line:#ececec;
  --soft:#f5f5f5;
  --white:#fff;
}
*{box-sizing:border-box;margin:0;padding:0}
html,body{width:1200px;height:2293px;overflow:hidden}
body{font-family:"Poppins",sans-serif;color:var(--ink);background:var(--white);position:relative}
.abs{position:absolute}

/* hero */
.hero{left:0;top:0;width:1200px;height:439px;background:linear-gradient(135deg,#3a4a84 0%,#2a376c 50%,#34427a 100%)}
.hero-title{left:0;top:240px;width:1200px;text-align:center;color:var(--white);font-size:56px;font-weight:600;letter-spacing:.5px}
.nav{left:90px;top:20px;width:1020px;height:59px;background:var(--white);display:flex;align-items:center}
.brand{margin-left:30px;font-size:15px;font-weight:700;color:var(--navy);display:flex;align-items:center;gap:6px}
.brand .dot{width:10px;height:10px;background:var(--blue)}
.menu{display:flex;margin-left:auto;height:59px}
.menu a{display:flex;align-items:center;padding:0 20px;font-size:13px;color:var(--ink);text-decoration:none}
.menu a.active{background:var(--blue);color:var(--white);font-weight:500}
.call{margin-left:152px;margin-right:28px;font-size:12.5px}
.call b{font-weight:600}

/* contact section */
.photo-cafe{left:98px;top:534px;width:375px;height:395px;background:linear-gradient(160deg,#9aa3ad 0%,#c7ccd2 40%,#5b6170 75%,#7d3a40 100%)}
.contact-box{left:98px;top:929px;width:375px;height:226px;background:var(--navy);color:var(--white);padding:42px 0 0 39px}
.contact-box h3{font-size:20px;font-weight:600;margin-bottom:14px}
.contact-row{display:flex;align-items:center;gap:22px;font-size:12.5px;font-weight:600;height:40px}
.contact-row svg{width:17px;height:17px;flex:none}

.form-card{left:521px;top:527px;width:589px;height:784px;border:1px solid var(--line);padding:0 40px}
.form-card h2{margin-top:42px;font-size:28px;font-weight:600;color:var(--blue)}
.form-card p{margin-top:16px;font-size:13px;line-height:21px;color:var(--text);width:510px}
.field{position:absolute;background:var(--field);height:44px;font-size:12.5px;color:#888;padding:14px 11px 0}
.f-first{left:40px;top:214px;width:246px}
.f-last{left:302px;top:214px;width:247px}
.f-email{left:40px;top:281px;width:509px}
.f-phone{left:40px;top:349px;width:509px}
.f-select{left:40px;top:416px;width:509px;color:#333;display:flex;justify-content:space-between;padding-right:14px}
.f-msg{left:40px;top:483px;width:509px;height:174px;padding-top:13px;padding-left:13px}
.send{position:absolute;left:40px;top:681px;width:142px;height:43px;background:#0d0806;color:var(--white);font-size:12.5px;font-weight:600;display:flex;align-items:center;justify-content:center}

/* services band */
.band{left:90px;top:1406px;width:510px;height:340px;background:var(--soft);padding:77px 0 0 48px}
.band .kicker{font-size:17px;font-weight:500;color:#333}
.band h2{font-size:28px;font-weight:600;color:var(--blue);margin-top:8px}
.band p{margin-top:24px;font-size:13px;line-height:21px;color:var(--text);width:410px}
.photo-sign{left:600px;top:1406px;width:510px;height:340px;background:linear-gradient(180deg,#b9cbd8 0%,#dfe6ec 35%,#8c94a0 70%,#3a4456 100%)}

/* footer */
.footer{left:0;top:1834px;width:1200px;height:459px;background:var(--soft)}
.f-brand{left:90px;top:1918px;font-size:26px;font-weight:700;color:var(--navy);display:flex;align-items:center;gap:10px}
.f-brand .dot{width:16px;height:16px;background:var(--blue)}
.f-about{left:90px;top:1992px;width:460px;font-size:13px;line-height:21px;color:#444}
.f-social-t{left:90px;top:2087px;font-size:13px;font-weight:600}
.f-social{left:90px;top:2118px;display:flex;gap:12px}
.f-social span{width:16px;height:16px;background:#555;border-radius:50%}
.f-col h4{font-size:16px;font-weight:600;margin-bottom:16px}
.f-services{left:600px;top:1914px}
.f-services li{list-style:none;font-size:13px;line-height:21px;color:#555}
.f-info{left:875px;top:1914px;width:210px}
.f-info h5{font-size:13px;font-weight:600;color:#333}
.f-info div{font-size:13px;line-height:21px;color:#555}
.copy{left:0;top:2258px;width:1200px;text-align:center;font-size:12px;color:#555}
</style>
</head>
<body>

<section class="abs hero" role="img" aria-label="Dimmed navy-tinted photo of the roadhaven building front with its sign"></section>
<h1 class="abs hero-title">Contact</h1>
<header class="abs nav">
  <div class="brand"><span class="dot"></span>Roadhaven 41Ter</div>
  <nav class="menu">
    <a href="#">Home</a><a href="#">Services</a><a href="#">About</a><a href="#">Blog</a><a href="#" class="active">Contact</a>
  </nav>
  <div class="call">Call us: <b>(123) 4567 890</b></div>
</header>

<div class="abs photo-cafe" role="img" aria-label="Photo of the café-restaurant facade with blue windows and red carpet"></div>
<aside class="abs contact-box">
  <h3>Contact us today</h3>
  <div class="contact-row">
    <svg viewBox="0 0 24 24" fill="#fff"><path d="M6.6 10.8a15.1 15.1 0 0 0 6.6 6.6l2.2-2.2a1 1 0 0 1 1-.25 11.4 11.4 0 0 0 3.6.57 1 1 0 0 1 1 1V20a1 1 0 0 1-1 1A17 17 0 0 1 3 4a1 1 0 0 1 1-1h3.5a1 1 0 0 1 1 1c0 1.25.2 2.45.57 3.57a1 1 0 0 1-.25 1z"/></svg>
    (123) 4567 890
  </div>
  <div class="contact-row">
    <svg viewBox="0 0 24 24" fill="none" stroke="#fff" stroke-width="2"><rect x="3" y="5" width="18" height="14" rx="1"/><path d="M3 6l9 7 9-7"/></svg>
    jobs@guardedroadhaven.eu
  </div>
  <div class="contact-row">
    <svg viewBox="0 0 24 24" fill="#fff"><path d="M12 2a6 6 0 0 0-6 6c0 4.5 6 11 6 11s6-6.5 6-11a6 6 0 0 0-6-6zm0 8.2A2.2 2.2 0 1 1 12 5.8a2.2 2.2 0 0 1 0 4.4z"/><rect x="3" y="20" width="18" height="2"/></svg>
    Harbour Lane 22 4170 Brakelmont
  </div>
</aside>

<section class="abs form-card">
  <h2>Send us a message</h2>
  <p>We value your feedback, inquiries, and suggestions. Feel free to reach out to us using the contact information below or by filling out the contact form. Our dedicated team is ready to assist you and provide any information you may need.</p>
  <div class="field f-first">First Name *</div>
  <div class="field f-last">Last Name *</div>
  <div class="field f-email">Your Email *</div>
  <div class="field f-phone">Your Phone Number</div>
  <div class="field f-select"><span>Select Service</span><span>⌄</span></div>
  <div class="field f-msg">Message *</div>
  <div class="send">Send Message</div>
</section>

<section class="abs band">
  <div class="kicker">High Quality</div>
  <h2>Services</h2>
  <p>We look forward to hearing from you and assisting you with any inquiries, reservations, or feedback you may have. Your satisfaction is our top priority, and we are here to provide you with exceptional service and support.</p>
</section>
<div class="abs photo-sign" role="img" aria-label="Photo of the building roofline and sign against a cloudy sky"></div>

<footer class="abs footer"></footer>
<div class="abs f-brand"><span class="dot"></span>Roadhaven 41Ter</div>
<p class="abs f-about">Step into a world of possibilities where convenience meets delight. At Roadhaven 41Ter, we are more than just a pit stop along the road. We are your versatile destination, catering to your every need and craving.</p>
<div class="abs f-social-t">Social</div>
<div class="abs f-social" aria-label="Social links"><span></span><span></span><span></span></div>
<div class="abs f-col f-services">
  <h4>Services</h4>
  <ul><li>Velko Express</li><li>Sandwich Bar</li><li>Restaurant</li><li>Parking Facilities</li><li>Meeting Rooms</li></ul>
</div>
<div class="abs f-col f-info">
  <h4>Contact Info</h4>
  <h5>Location</h5>
  <div style="margin-top:18px">Havenweg 22, 4170 Brakelmont</div>
  <h5 style="margin-top:20px">Opening Hours</h5>
  <div>8:00 AM-18:00 PM</div>
  <h5 style="margin-top:20px">Phone Number</h5>
  <div>(123) 4567 890</div>
</div>
<div class="abs copy">Copyright © 2023 - Roadhaven41TER</div>

</body>
</html>
```